ALL TYPES OF COMMERCIAL PLASTERING

TYPE OF BLOCK LETTERING WITH STAND OUT QUALITIES
WITH SOME TYPE OF LOGO
SOMETHING UNIQUE FOR THE BUILDING INDUSTRY.
QUALITY WORKMANSHIP
Updates

forgot to include my mobile phone number on my brief. could you add it to your design please MOBILE PH 0491 586 032

please let me make this quite clear ,the company name is harbourline linings and Fitouts PTY LTD. THE TYPE OF WORK WE WILL BE DOING IS COMMERCIAL PLASTERING.

Industry/Entity Type

Industry

Contact Information for Business Card

harbourline linings and fitouts P/L
marcus trelawny p.o.box 82 wendouree 3355 email address harbourlinelinings@mailcove.example
ABN 84 519 263 740 COMMERCIAL PLASTERING

```html
<!DOCTYPE html>
<html lang="en">
<head>
<meta charset="utf-8">
<title>Harbourline Linings and Fitouts – Business Card</title>
<link rel="stylesheet" href="https://fonts.googleapis.com/css2?family=Cinzel:wght@700&family=Montserrat:wght@300;400;500&display=swap">
<style>
  :root {
    --stage: #e9e7e4;
    --card-black: #030303;
    --card-white: #f4f4f4;
    --accent: #a4c31f;
    --ink-light: #f2f2f2;
  }
  * { margin: 0; padding: 0; box-sizing: border-box; }
  html, body { width: 1200px; height: 848px; overflow: hidden; background: var(--stage); }
  .canvas { position: relative; width: 1200px; height: 848px; }
  .card {
    position: absolute; left: 100px; top: 138px; width: 1000px; height: 572px;
    border-radius: 30px; overflow: hidden; background: var(--card-black);
    box-shadow: 0 18px 40px rgba(0,0,0,.25);
  }
  .card__strip { position: absolute; left: 0; top: 0; bottom: 0; width: 150px; background: var(--card-white); }
  .card__rule { position: absolute; left: 150px; top: 0; bottom: 0; width: 14px; background: var(--accent); }
  .brand-dot {
    position: absolute; left: 100px; top: 58px; width: 124px; height: 124px;
    border-radius: 50%; background: var(--accent);
  }
  .brand { position: absolute; left: 250px; top: 62px; }
  .brand__name {
    font-family: "Cinzel", serif; font-weight: 700; color: var(--accent);
    font-size: 46px; line-height: 1.02; text-transform: uppercase; letter-spacing: 1px;
  }
  .brand__trade {
    margin-top: 12px; font-family: "Montserrat", sans-serif; font-weight: 400;
    font-size: 19px; letter-spacing: 1px; color: var(--ink-light); text-transform: uppercase;
  }
  .person {
    position: absolute; left: 250px; top: 246px; font-family: "Montserrat", sans-serif;
    font-weight: 300; font-size: 38px; color: var(--ink-light);
  }
  .contacts { position: absolute; left: 250px; top: 336px; list-style: none; }
  .contacts li {
    display: flex; align-items: center; height: 50px;
    font-family: "Montserrat", sans-serif; font-weight: 300; font-size: 27px; color: var(--ink-light);
  }
  .contacts svg { width: 26px; height: 26px; margin-right: 26px; fill: var(--accent); flex: none; }
</style>
</head>
<body>
<div class="canvas">
  <section class="card" aria-label="Business card">
    <div class="card__strip"></div>
    <div class="card__rule"></div>
    <div class="brand-dot"></div>
    <div class="brand">
      <div class="brand__name">Harbourline Linings<br>and Fitouts P/L</div>
      <div class="brand__trade">Commercial Plastering</div>
    </div>
    <div class="person">marcus trelawny</div>
    <ul class="contacts">
      <li>
        <svg viewBox="0 0 24 24" aria-hidden="true"><path d="M7 1h10a2 2 0 0 1 2 2v18a2 2 0 0 1-2 2H7a2 2 0 0 1-2-2V3a2 2 0 0 1 2-2zm0 3v9h10V4zm1 11v2h2v-2zm3 0v2h2v-2zm3 0v2h2v-2zm-6 3v2h2v-2zm3 0v2h2v-2zm3 0v2h2v-2z"/></svg>
        0491 586 032
      </li>
      <li>
        <svg viewBox="0 0 24 24" aria-hidden="true"><path d="M12 1a8 8 0 0 0-8 8c0 6 8 14 8 14s8-8 8-14a8 8 0 0 0-8-8zm0 11a3 3 0 1 1 0-6 3 3 0 0 1 0 6z"/></svg>
        ABN 84 519 263 740
      </li>
      <li>
        <svg viewBox="0 0 24 24" aria-hidden="true"><path d="M12 2 1 12h3v10h6v-6h4v6h6V12h3z"/></svg>
        p.o.box 82 wendouree 3355
      </li>
      <li>
        <svg viewBox="0 0 24 24" aria-hidden="true"><path d="M1 5h22v14H1zm2 2v.5l9 6 9-6V7zm0 3v7h18v-7l-9 6z"/></svg>
        harbourlinelinings@mailcove.example
      </li>
    </ul>
  </section>
</div>
</body>
</html>
```